Business Card for Canopy Kin-Eco Friendly Organic Clothing Brand

We are looking for an amazing business card for our eco friendly, organic clothing brand. We are thinking maybe a business card with a peel off sticker on the back, since our hanging clothing tag is a peel off sticker on the back. I will attach our hang tag so we can make sure we stay in line with our design. I've also attached a bag we are doing because I do like the scattered emblem look as well.

```html
<!DOCTYPE html>
<html lang="en">
<head>
<meta charset="utf-8">
<title>Canopy Kin – Business Card</title>
<link href="https://fonts.googleapis.com/css2?family=Source+Sans+3:wght@400;600;700&display=swap" rel="stylesheet">
<style>
  :root {
    --page-bg: #ece9e4;
    --gold-light: #ecd189;
    --gold-pale: #f2dd9c;
    --gold-mid: #ddb65a;
    --gold-deep: #cc9f3a;
    --gold-emblem: #e4c26f;
    --ink: #1c1a16;
    --ink-soft: #2a2620;
  }
  * { box-sizing: border-box; margin: 0; padding: 0; }
  html, body {
    width: 1200px;
    height: 900px;
    overflow: hidden;
    background: var(--page-bg);
    font-family: "Source Sans 3", "Myriad Pro", sans-serif;
    color: var(--ink);
  }
  .canvas { position: relative; width: 1200px; height: 900px; }

  .card {
    position: absolute;
    box-shadow: 0 6px 18px rgba(0,0,0,0.18);
  }

  /* Front */
  .card-front {
    left: 238px; top: 62px;
    width: 555px; height: 342px;
    background: linear-gradient(180deg, var(--gold-light) 0%, var(--gold-mid) 70%, var(--gold-deep) 100%);
  }
  .contact-block {
    position: absolute;
    left: 43px; top: 78px;
  }
  .person-name {
    font-size: 20px;
    font-weight: 700;
    line-height: 24px;
  }
  .person-title {
    font-size: 15px;
    line-height: 20px;
    color: var(--ink-soft);
  }
  .contact-list {
    list-style: none;
    margin-top: 22px;
  }
  .contact-list li {
    display: flex;
    align-items: center;
    font-size: 15px;
    line-height: 20px;
    color: var(--ink-soft);
  }
  .contact-icon {
    width: 11px; height: 11px;
    margin-right: 11px;
    flex: none;
  }
  .address {
    margin-top: 20px;
    font-size: 15px;
    line-height: 20px;
    font-style: normal;
    color: var(--ink-soft);
  }
  .brand-mark {
    position: absolute;
    left: 282px; top: 150px;
    display: flex;
    align-items: center;
    gap: 12px;
  }
  .brand-square {
    width: 22px; height: 22px;
    background: var(--ink);
  }
  .brand-name {
    font-size: 34px;
    font-weight: 700;
    color: var(--ink);
    line-height: 1;
  }
  .brand-url {
    position: absolute;
    left: 380px; top: 202px;
    font-size: 9px;
    color: var(--ink-soft);
  }

  /* Back */
  .card-back {
    left: 457px; top: 518px;
    width: 560px; height: 342px;
    background: radial-gradient(ellipse 220px 180px at 50% 42%, var(--gold-light) 0%, var(--gold-mid) 55%, var(--gold-deep) 100%);
  }
  .back-emblem {
    position: absolute;
    left: 173px; top: 44px;
    width: 212px; height: 216px;
    border-radius: 50%;
    background: radial-gradient(circle at 50% 50%, var(--gold-pale) 0%, var(--gold-emblem) 55%, rgba(228,194,111,0) 72%);
    box-shadow: inset 0 0 0 1px rgba(150,110,30,0.25);
  }
  .back-name {
    position: absolute;
    left: 0; right: 0; top: 276px;
    text-align: center;
    font-size: 34px;
    font-weight: 600;
    line-height: 40px;
    color: var(--gold-pale);
  }
</style>
</head>
<body>
<main class="canvas">

  <section class="card card-front" aria-label="Business card front">
    <div class="contact-block">
      <h1 class="person-name">Jonathan Smith</h1>
      <p class="person-title">Managing Director</p>
      <ul class="contact-list">
        <li>
          <svg class="contact-icon" viewBox="0 0 24 24" aria-hidden="true"><path fill="#1c1a16" d="M6.6 10.8a15.1 15.1 0 0 0 6.6 6.6l2.2-2.2a1 1 0 0 1 1-.25 11.4 11.4 0 0 0 3.6.57 1 1 0 0 1 1 1V20a1 1 0 0 1-1 1A17 17 0 0 1 3 4a1 1 0 0 1 1-1h3.5a1 1 0 0 1 1 1c0 1.25.2 2.45.57 3.57a1 1 0 0 1-.25 1z"/></svg>
          044-123 456 789
        </li>
        <li>
          <svg class="contact-icon" viewBox="0 0 24 24" aria-hidden="true"><rect x="2" y="5" width="20" height="14" fill="#1c1a16"/><path d="M3 6l9 7 9-7" fill="none" stroke="#e2bd66" stroke-width="2"/></svg>
          info@webname.com
        </li>
        <li>
          <svg class="contact-icon" viewBox="0 0 24 24" aria-hidden="true"><circle cx="12" cy="12" r="11" fill="#1c1a16"/></svg>
          www.websitename.com
        </li>
      </ul>
      <address class="address">12345, Address Goes Here<br>Country Name, 123456.</address>
    </div>

    <div class="brand-mark">
      <span class="brand-square" aria-hidden="true"></span>
      <span class="brand-name">Canopy Kin</span>
    </div>
    <p class="brand-url">www.canopykin.com</p>
  </section>

  <section class="card card-back" aria-label="Business card back">
    <div class="back-emblem" role="img" aria-label="Embossed emblem of a seated meditating figure"></div>
    <p class="back-name">Canopy Kin</p>
  </section>

</main>
</body>
</html>
```